Building company buisness cards

We are looking for a sharp modern new look for our business cards.We are a New Zealand based company that specialises in house and land packages.We have attached a photo of the current logo and would like to see if it can be improved somehow if needed.We are open to any colours but we have chosen Black and White at this stage. Feel free to change the font and make the logo smarter looking.Play with the colours and see what looks best.We want a card that looks so good know one will want to throw it away!

Target Market(s)

Building profesonals, home buyers

Industry/Entity Type

Building

Contact Information for Business Card

Garrick Tenwood
0275390628
garrickt@hartvale.co.nz

Font styles to use
Serif
Sans Serif

Colors

Designer to choose colors to be used in the design.

Requirements
Must have
• Just the logo on one side and details on the other
• Clean simple looking card
Nice to have
• Round corners and detail like raised or spot UV
• Something that stands out
Should not have
• To title needed, Director etc

```html
<!DOCTYPE html>
<html lang="en">
<head>
<meta charset="utf-8">
<title>Hartvale Business Cards</title>
<link href="https://fonts.googleapis.com/css2?family=Roboto:wght@400;500&display=swap" rel="stylesheet">
<style>
  :root {
    --backdrop: #262626;
    --card-white: #ffffff;
    --brand-blue: #045a98;
    --brand-orange: #ec9c24;
    --text-grey: #4a4a4a;
    --rule-grey: #c9c9c9;
  }
  * { margin: 0; padding: 0; box-sizing: border-box; }
  html, body {
    width: 1125px;
    height: 1200px;
    overflow: hidden;
    background: var(--backdrop);
    font-family: "Roboto", Arial, sans-serif;
  }
  .canvas { position: relative; width: 1125px; height: 1200px; }

  .card {
    position: absolute;
    left: 156px;
    width: 825px;
    height: 471px;
    border-radius: 26px;
    overflow: hidden;
  }
  .card-front { top: 106px; background: var(--card-white); }
  .card-back { top: 639px; background: var(--brand-orange); }

  /* Front */
  .brand-lockup {
    position: absolute;
    left: 92px;
    top: 196px;
    display: flex;
    align-items: center;
    gap: 16px;
  }
  .brand-name {
    font-size: 64px;
    font-weight: 400;
    color: var(--brand-blue);
    line-height: 1;
    letter-spacing: -0.5px;
  }
  .brand-dot {
    width: 52px;
    height: 52px;
    border-radius: 50%;
    border: 4px solid var(--brand-orange);
  }
  .divider {
    position: absolute;
    left: 457px;
    top: 152px;
    width: 1px;
    height: 170px;
    background: var(--rule-grey);
  }
  .contact-block { position: absolute; left: 494px; top: 170px; }
  .person-name {
    font-size: 30px;
    font-weight: 500;
    color: var(--brand-blue);
    line-height: 1;
    margin-bottom: 24px;
  }
  .contact-list { list-style: none; }
  .contact-item {
    display: flex;
    align-items: center;
    gap: 11px;
    height: 26px;
    font-size: 19.5px;
    color: var(--text-grey);
  }
  .contact-icon { width: 19px; height: 19px; flex: none; fill: var(--brand-blue); }

  /* Back */
  .back-lockup {
    position: absolute;
    left: 0;
    right: 0;
    top: 196px;
    display: flex;
    justify-content: center;
    align-items: center;
    gap: 18px;
  }
  .back-name {
    font-size: 66px;
    font-weight: 400;
    color: var(--card-white);
    line-height: 1;
  }
  .back-dot {
    width: 54px;
    height: 54px;
    border-radius: 50%;
    border: 5px solid var(--card-white);
  }
  .back-url {
    position: absolute;
    left: 0;
    right: 0;
    top: 404px;
    text-align: center;
    font-size: 19px;
    letter-spacing: 0.48em;
    color: var(--card-white);
  }
</style>
</head>
<body>
<main class="canvas">
  <section class="card card-front" aria-label="Card front">
    <div class="brand-lockup">
      <span class="brand-name">Hartvale</span>
      <span class="brand-dot"></span>
    </div>
    <div class="divider"></div>
    <div class="contact-block">
      <h1 class="person-name">Garrick Tenwood</h1>
      <ul class="contact-list">
        <li class="contact-item">
          <svg class="contact-icon" viewBox="0 0 24 24" aria-hidden="true"><path d="M6.6 10.8c1.4 2.8 3.8 5.1 6.6 6.6l2.2-2.2c.3-.3.7-.4 1-.2 1.1.4 2.3.6 3.6.6.6 0 1 .4 1 1V20c0 .6-.4 1-1 1C10.6 21 3 13.4 3 4c0-.6.4-1 1-1h3.5c.6 0 1 .4 1 1 0 1.3.2 2.5.6 3.6.1.3 0 .7-.2 1z"/></svg>
          <span>0275390628</span>
        </li>
        <li class="contact-item">
          <svg class="contact-icon" viewBox="0 0 24 24" aria-hidden="true"><path d="M2 6h20v12H2z M3.5 7.5 12 13l8.5-5.5" fill="none" stroke="#045a98" stroke-width="2"/></svg>
          <span>garrickt@hartvale.co.nz</span>
        </li>
        <li class="contact-item">
          <svg class="contact-icon" viewBox="0 0 24 24" aria-hidden="true"><circle cx="12" cy="12" r="10"/><path d="M7 7c2 0 3 1 2.5 2.5S7 11 8 13s3 1 3 3-1 3-1 4" fill="none" stroke="#fff" stroke-width="1.6"/><path d="M15 5c-1 1.5 0 3 1.5 3s2 2 1 3.5" fill="none" stroke="#fff" stroke-width="1.6"/></svg>
          <span>www.hartvale.co.nz</span>
        </li>
      </ul>
    </div>
  </section>

  <section class="card card-back" aria-label="Card back">
    <div class="back-lockup">
      <span class="back-name">Hartvale</span>
      <span class="back-dot"></span>
    </div>
    <p class="back-url">www.Hartvale.co.nz</p>
  </section>
</main>
</body>
</html>
```